Confidential Pitch Deck- Pierloft- Peer to Peer Boat Dock and Slip Rentals

We are looking for a redesign for a pitch deck for fund raising purposes. This is for a maritime dock rental company similar to stayvane for private boat and dock slips. The company is called Pierloft.app and is currently in a growth round of funding. We have included an empty version of the deck (no text) and will send the current pitch deck directly designers that we decide to work with. We have placed an example of a deck we like too below as well.

Target Market(s)

Two-sided Market Investors, Boater and Private Dock and Slip Owners

Industry/Entity Type

Peer to Peer property sharing, prop tech

Font styles to use
Serif

Colors
0054AA
0677BA
7BADD7
CADEEF
E8F1F8
FFC000
F8CF3A
FAE287
FDF2CF
FEFAEE

Requirements
Must have
• Our Logo, Our colors, clean text color with vibrant backgrounds
Nice to have
• Boats and boat docks and slips in the same picture in Florida and up and down the east coast

```html
<!DOCTYPE html>
<html lang="en">
<head>
<meta charset="utf-8">
<title>Pierloft — Pitch Deck</title>
<link href="https://fonts.googleapis.com/css2?family=Merriweather:wght@400;700;900&display=swap" rel="stylesheet">
<style>
:root{
  --navy:#0054aa;
  --navy-deep:#003f80;
  --navy-soft:rgba(0,84,170,.92);
  --blue-mid:#0677ba;
  --blue-light:#7badd7;
  --blue-pale:#e8f1f8;
  --yellow:#ffc000;
  --yellow-soft:#f8cf3a;
  --white:#ffffff;
  --ink:#1b2a3a;
  --muted:#5f6b78;
  --line:#cadeef;
  --page:#ffffff;
}
*{box-sizing:border-box;margin:0;padding:0}
html,body{width:1200px;height:4144px;overflow:hidden;background:var(--page);font-family:'Merriweather',serif;color:var(--ink)}
.slide{position:absolute;left:28px;width:1140px;height:640px;overflow:hidden;background:var(--white);box-shadow:0 0 6px rgba(0,0,0,.12)}
.abs{position:absolute}
.brand{position:absolute;display:flex;align-items:center;gap:14px;font-weight:900;letter-spacing:2px;color:var(--navy);text-transform:uppercase}
.brand .dot{border-radius:50%;background:var(--navy)}
.brand.light{color:var(--white)}
.brand.light .dot{background:var(--white)}
.photo{position:absolute}
.heading{position:absolute;font-weight:900;color:var(--yellow);text-transform:uppercase;text-align:center;letter-spacing:1px}
.contact{display:flex;align-items:center;gap:10px;font-weight:700;font-size:17px}
.contact .ico{width:16px;height:20px;border-radius:3px;background:var(--yellow)}
/* cover */
.cover-box{left:54px;top:210px;width:664px;height:257px;background:var(--navy);color:var(--white);font-weight:900;font-size:40px;line-height:58px;padding:42px 34px;text-transform:uppercase;white-space:nowrap}
/* mission */
.mission-band{left:0;top:173px;width:1064px;height:291px;background:var(--navy-soft)}
.mission-title{left:64px;top:254px;font-weight:900;font-size:50px;line-height:62px;color:var(--yellow)}
.mission-copy{left:373px;top:252px;width:620px;font-size:16.5px;line-height:30px;color:var(--white)}
/* team */
.card{position:absolute;width:243px;height:207px;background:var(--white);border:1px solid var(--line);box-shadow:0 1px 4px rgba(0,0,0,.08);text-align:center}
.card .avatar{width:112px;height:112px;border-radius:50%;border:4px solid var(--yellow);background:linear-gradient(160deg,#cadeef,#7badd7);margin:14px auto 12px}
.card .name{font-weight:700;font-size:18px}
.card .role{font-size:14px;color:var(--muted);margin-top:6px}
.card.lead{width:497px;background:var(--navy);border:none;text-align:left;color:var(--white)}
.card.lead .avatar{position:absolute;left:26px;top:15px;width:176px;height:176px;margin:0}
.card.lead .name{position:absolute;left:226px;top:72px;font-size:20px}
.card.lead .role{position:absolute;left:226px;top:110px;color:var(--white);font-size:15px}
/* ask */
.ask-band{left:0;top:285px;width:1140px;height:355px;background:var(--navy)}
.ask-step{position:absolute;width:272px;height:272px;border-radius:50%;background:var(--yellow);border:6px solid var(--navy);display:flex;align-items:center;justify-content:center}
.ask-label{position:absolute;width:300px;text-align:center;color:var(--white);font-weight:700;font-size:17px;line-height:27px}
/* solution */
.solution{background:var(--navy)}
.solution .photo{inset:0;background:linear-gradient(180deg,#0a5fae 0%,#0054aa 45%,#003f80 100%)}
.item{position:absolute;display:flex;align-items:center;gap:18px;color:var(--white);font-weight:700;font-size:15px;line-height:21px}
.item .num{font-weight:900;font-size:96px;line-height:100px;color:var(--yellow);width:74px}
/* thanks */
.thanks .photo{inset:0;background:linear-gradient(180deg,#7badd7 0%,#cadeef 38%,#fae287 56%,#8a6a4c 78%,#4a3a30 100%)}
.thanks-panel{left:166px;top:149px;width:807px;height:331px;background:rgba(0,84,170,.9);display:flex;flex-direction:column;align-items:center;color:var(--white)}
.social{width:40px;height:40px;border-radius:50%;border:2px solid var(--white)}
</style>
</head>
<body>

<section class="slide" style="top:22px">
  <div class="brand" style="left:59px;top:92px;font-size:42px"><span class="dot" style="width:72px;height:72px"></span>Pierloft</div>
  <div class="abs cover-box">Peer to peer boat<br>dock and slip<br>rentals Cole Ray</div>
  <div class="abs" style="left:92px;top:504px;display:flex;gap:56px">
    <span class="contact"><span class="ico"></span>cole@pierloft.app</span>
    <span class="contact"><span class="ico"></span>pierloft.app</span>
  </div>
  <div class="photo" role="img" aria-label="Wooden dock leading out onto a calm forest lake" style="left:598px;top:0;width:416px;height:640px;background:linear-gradient(180deg,#0677ba 0%,#7badd7 30%,#5a7f6a 42%,#7badd7 55%,#9a6a4e 75%,#b27a5a 100%)"></div>
</section>

<section class="slide" style="top:696px">
  <div class="brand" style="left:35px;top:42px;font-size:28px"><span class="dot" style="width:48px;height:48px"></span>Pierloft</div>
  <div class="photo" role="img" aria-label="Lake dock at sunset with mountains and pine forest" style="left:570px;top:0;width:570px;height:640px;background:linear-gradient(180deg,#7badd7 0%,#fae287 18%,#2f4d35 30%,#0677ba 55%,#3a6f82 70%,#8a6a4c 85%,#6f553e 100%)"></div>
  <div class="abs mission-band"></div>
  <div class="abs mission-title">OUR<br>MISSION</div>
  <p class="abs mission-copy">Pierloft facilitates safe and hassle-free boating experiences by connecting boat owners with private docks and marina slips. Our platform ensures secure transactions for owners renting to fellow boaters, offering opportunities for spontaneous adventures and long-term docking solutions.</p>
</section>

<section class="slide" style="top:1424px">
  <div class="brand" style="left:35px;top:36px;font-size:28px"><span class="dot" style="width:48px;height:48px"></span>Pierloft</div>
  <h2 class="heading" style="left:0;width:1140px;top:62px;font-size:40px">Our Team</h2>
  <div class="card lead" style="left:64px;top:141px"><div class="avatar" role="img" aria-label="Portrait of Cole"></div><div class="name">Cole</div><div class="role">CEO Cofounder,</div></div>
  <div class="card" style="left:573px;top:141px"><div class="avatar" role="img" aria-label="Portrait of Tessa"></div><div class="name">Tessa</div><div class="role">Marketing</div></div>
  <div class="card" style="left:827px;top:141px"><div class="avatar" role="img" aria-label="Portrait of Mira"></div><div class="name">Mira</div><div class="role">Product</div></div>
  <div class="card" style="left:64px;top:362px"><div class="avatar" role="img" aria-label="Portrait of Dana"></div><div class="name">Dana</div><div class="role">Customer Exp</div></div>
  <div class="card" style="left:318px;top:362px"><div class="avatar" role="img" aria-label="Portrait of Brynn"></div><div class="name">Brynn</div><div class="role">Marketing</div></div>
  <div class="card" style="left:573px;top:362px"><div class="avatar" role="img" aria-label="Portrait of Owen"></div><div class="name">Owen</div><div class="role">Technology</div></div>
  <div class="card" style="left:827px;top:362px"><div class="avatar" role="img" aria-label="Portrait of Reid"></div><div class="name">Reid</div><div class="role">Growth</div></div>
</section>

<section class="slide" style="top:2106px">
  <div class="brand" style="left:35px;top:36px;font-size:28px"><span class="dot" style="width:48px;height:48px"></span>Pierloft</div>
  <h2 class="heading" style="left:0;width:1140px;top:62px;font-size:40px">The Ask</h2>
  <div class="abs ask-band"></div>
  <div class="ask-step" style="left:59px;top:150px">
    <svg width="120" height="130" viewBox="0 0 120 130" fill="none" stroke="#0054aa" stroke-width="7" stroke-linejoin="round" stroke-linecap="round"><rect x="20" y="18" width="70" height="100" rx="6" fill="#0054aa"/><path d="M36 42h10M56 42h22M36 64h10M56 64h22M36 86h10M56 86h22" stroke="#ffc000" stroke-width="6"/><circle cx="96" cy="36" r="14" fill="#ffc000"/><path d="M89 36l5 5 9-10"/></svg>
  </div>
  <div class="ask-step" style="left:432px;top:150px">
    <svg width="130" height="130" viewBox="0 0 130 130"><rect x="10" y="20" width="110" height="100" rx="10" fill="#0054aa"/><g fill="#ffc000"><rect x="24" y="56" width="20" height="18" rx="3"/><rect x="86" y="56" width="20" height="18" rx="3"/><rect x="24" y="86" width="20" height="18" rx="3"/><rect x="55" y="86" width="20" height="18" rx="3"/><rect x="86" y="86" width="20" height="18" rx="3"/></g><path d="M55 64l7 7 12-14" stroke="#ffc000" stroke-width="6" fill="none" stroke-linecap="round"/><g fill="#0054aa"><rect x="28" y="8" width="8" height="22" rx="3"/><rect x="50" y="8" width="8" height="22" rx="3"/><rect x="72" y="8" width="8" height="22" rx="3"/><rect x="94" y="8" width="8" height="22" rx="3"/></g></svg>
  </div>
  <div class="ask-step" style="left:794px;top:150px">
    <svg width="130" height="130" viewBox="0 0 130 130"><g fill="#0054aa"><circle cx="65" cy="18" r="16"/><circle cx="20" cy="62" r="16"/><circle cx="110" cy="62" r="16"/><circle cx="65" cy="76" r="14"/><path d="M40 122a25 25 0 0 1 50 0z"/></g><g fill="none" stroke="#0054aa" stroke-width="5" stroke-linecap="round"><path d="M45 22a48 48 0 0 0-22 22"/><path d="M85 22a48 48 0 0 1 22 22"/><path d="M24 84a42 42 0 0 0 16 18"/><path d="M106 84a42 42 0 0 1-16 18"/></g></svg>
  </div>
  <div class="ask-label" style="left:45px;top:462px">List Your Dock</div>
  <div class="ask-label" style="left:418px;top:468px">Watch as the<br>Bookings Roll In.</div>
  <div class="ask-label" style="left:780px;top:468px">Safely Earn<br>Extra Income!</div>
</section>

<section class="slide solution" style="top:2778px">
  <div class="photo" role="img" aria-label="Faint view of a wooden dock on a misty lake"></div>
  <div class="brand light" style="left:35px;top:36px;font-size:28px"><span class="dot" style="width:48px;height:48px"></span>Pierloft</div>
  <h2 class="heading" style="left:0;width:1140px;top:62px;font-size:40px">Our Solution</h2>
  <div class="item" style="left:64px;top:150px"><span class="num">1</span><span>Access to the largest listing of private<br>docks and slips</span></div>
  <div class="item" style="left:64px;top:290px"><span class="num">2</span><span>Flexible On-Demand Bookings</span></div>
  <div class="item" style="left:64px;top:426px"><span class="num">3</span><span>Online Platform Connection</span></div>
  <div class="item" style="left:605px;top:150px"><span class="num">4</span><span>Convenience and Cost Savings</span></div>
  <div class="item" style="left:605px;top:290px"><span class="num">5</span><span>Insurance for Damage Protection</span></div>
  <div class="item" style="left:605px;top:426px"><span class="num">6</span><span>Income Opportunities for<br>Dock Owners</span></div>
</section>

<section class="slide thanks" style="top:3440px">
  <div class="photo" role="img" aria-label="Wooden dock and moored boat on a lake at dusk"></div>
  <div class="abs thanks-panel">
    <div class="brand light" style="position:static;margin-top:40px;font-size:40px"><span class="dot" style="width:68px;height:68px"></span>Pierloft</div>
    <div style="font-weight:900;font-size:40px;margin-top:18px;letter-spacing:1px">THANK YOU</div>
    <div style="display:flex;gap:56px;margin-top:18px">
      <span class="contact"><span class="ico" style="background:var(--white)"></span>cole@pierloft.app</span>
      <span class="contact"><span class="ico" style="background:var(--white)"></span>pierloft.app</span>
    </div>
    <div style="display:flex;gap:20px;margin-top:26px">
      <span class="social"></span><span class="social"></span><span class="social"></span>
    </div>
  </div>
</section>

</body>
</html>
```